Kestrel Facilities Business Card Design

We would now like to design business cards with the new Kestrel Facilities logo

Target Market(s)

Professional

Industry/Entity Type

Professional services

Contact Information for Business Card

Employee name, title, phone number, email address, corporate office address and logo.

Font styles to use
Sans Serif

Colors
0054AA
0677BA
7BADD7
CADEEF
E8F1F8

Requirements
Must have
• My logo
Should not have
• any other pictures or images besides my logo

```html
<!DOCTYPE html>
<html lang="en">
<head>
<meta charset="utf-8">
<title>Kestrel Facilities Business Card</title>
<link rel="stylesheet" href="https://fonts.googleapis.com/css2?family=Montserrat:wght@400;500;700&display=swap">
<style>
  :root {
    --brand-blue: #0677BA;
    --brand-deep: #0054AA;
    --brand-soft: #7BADD7;
    --band-grey: #B9BCC0;
    --ink: #1c1c1c;
    --paper: #ffffff;
    --backdrop: #d9dcdf;
  }
  * { box-sizing: border-box; margin: 0; padding: 0; }
  html, body {
    width: 1200px; height: 900px; overflow: hidden;
    background: var(--backdrop);
    font-family: "Montserrat", sans-serif;
  }
  .sheet { position: relative; width: 1200px; height: 900px; }
  .card {
    position: absolute;
    width: 600px; height: 343px;
    background: var(--paper);
    border-radius: 22px;
    overflow: hidden;
    box-shadow: 0 10px 24px rgba(0,0,0,.18);
  }
  .card--back { left: 70px; top: 70px; }
  .card--front { left: 530px; top: 480px; }

  .wordmark {
    display: flex; align-items: center; gap: 12px;
    color: var(--brand-blue);
    font-weight: 700;
    letter-spacing: .02em;
  }
  .wordmark__square {
    width: 26px; height: 26px; border: 4px solid var(--brand-blue);
  }
  .card--back .wordmark {
    position: absolute; left: 0; right: 0; top: 0; bottom: 0;
    justify-content: center; font-size: 38px;
  }
  .card--front .wordmark {
    position: absolute; left: 34px; top: 124px; font-size: 25px;
  }
  .card--front .wordmark__square { width: 22px; height: 22px; border-width: 3px; }

  .divider {
    position: absolute; left: 292px; top: 52px;
    width: 2px; height: 176px; background: var(--brand-blue);
  }
  .details { position: absolute; left: 318px; top: 50px; color: var(--ink); }
  .details__name {
    color: var(--brand-blue); font-weight: 700; font-size: 20px;
    text-transform: uppercase; letter-spacing: .01em;
  }
  .details__title { font-size: 14px; margin-top: 2px; }
  .details__address { font-size: 14px; line-height: 1.3; margin-top: 16px; }
  .contact { list-style: none; margin-top: 16px; font-size: 14px; }
  .contact li { display: flex; align-items: center; gap: 8px; line-height: 1.45; }
  .contact svg { width: 13px; height: 13px; fill: var(--brand-blue); flex: none; }

  .band { position: absolute; left: 0; bottom: 0; width: 600px; height: 100px; }
</style>
</head>
<body>
<main class="sheet">
  <section class="card card--back" aria-label="Card back">
    <div class="wordmark"><span class="wordmark__square"></span>Kestrel Facilities</div>
  </section>

  <section class="card card--front" aria-label="Card front">
    <div class="wordmark"><span class="wordmark__square"></span>Kestrel Facilities</div>
    <div class="divider"></div>
    <div class="details">
      <p class="details__name">Dana Whitlow</p>
      <p class="details__title">Co-Founder</p>
      <p class="details__address">1482 Harbor View Lane<br>Suite 310 Ashford.42</p>
      <ul class="contact">
        <li><svg viewBox="0 0 16 16"><path d="M3 1h3l1.5 4-2 1.3a9 9 0 0 0 4.2 4.2L11 8.5l4 1.5v3a2 2 0 0 1-2 2A12 12 0 0 1 1 3a2 2 0 0 1 2-2z"/></svg>+1-555-014-2290</li>
        <li><svg viewBox="0 0 16 16"><path d="M1 3h14v10H1z M1 3l7 6 7-6" fill="none" stroke="#0677BA" stroke-width="1.6"/></svg>info@kestrelfac.com</li>
        <li><svg viewBox="0 0 16 16"><circle cx="8" cy="8" r="7"/></svg>www.kestrelfac.com</li>
      </ul>
    </div>
    <svg class="band" viewBox="0 0 600 100" preserveAspectRatio="none" aria-hidden="true">
      <polygon points="0,72 455,50 470,30 600,22 600,100 0,100" fill="var(--band-grey)"/>
      <polygon points="0,82 470,58 490,30 600,22 600,100 0,100" fill="var(--brand-blue)"/>
    </svg>
  </section>
</main>
</body>
</html>
```